Mira Bloom Fitness Coaching Project

I am a personal trainer based in London. My services include one-on-one PT sessions, bootcamps.
I would like the design to be minimalistic. With light colours: white, pink, purple.
I specialise in weight loss, flexibility, mobility.

Tessa Brogan
Personal Trainer
Email: tessa.brogan@quellmail.com
tel: 07700218493
Instagram: Mira Bloom

Target Market(s)

adults, mostly females (age 18-50).

Industry/Entity Type

Fitness

Contact Information for Business Card

Tessa Brogan
Personal Trainer
tel: 07700218493
Instagram: Mira Bloom

Font styles to use
Serif

Colors
eea4c8
fbd4d5
fdf9cf
cfeae6
cee9f5

Requirements
Nice to have
• minimalistic style
• easy to read and remember

```html
<!DOCTYPE html>
<html lang="en">
<head>
<meta charset="utf-8">
<title>Tessa Brogan – Personal Trainer Business Card</title>
<link rel="stylesheet" href="https://fonts.googleapis.com/css2?family=Lora:wght@400;500;700&display=swap">
<style>
  :root {
    --backdrop: #e4e4e4;
    --card: #ffffff;
    --pink: #eea4c8;
    --pink-deep: #d383ab;
    --blush: #fbd4d5;
    --ink: #6e6a6c;
    --photo-dark: #5b6b4a;
    --photo-mid: #b98a6a;
    --photo-light: #f1dcc4;
    --photo-frame: #3a3336;
  }
  * { box-sizing: border-box; margin: 0; padding: 0; }
  html, body {
    width: 1200px;
    height: 900px;
    overflow: hidden;
    background: var(--backdrop);
  }
  .canvas {
    position: relative;
    width: 1200px;
    height: 900px;
  }
  .business-card {
    position: absolute;
    left: 150px;
    top: 193px;
    width: 900px;
    height: 514px;
    background: var(--card);
    border-radius: 26px;
    box-shadow: 0 10px 30px rgba(0,0,0,0.14);
    border-bottom: 10px solid var(--pink);
    font-family: "Lora", Georgia, serif;
  }
  .portrait {
    position: absolute;
    left: 470px;
    top: 30px;
    width: 400px;
    height: 330px;
    border-radius: 26px;
    border: 3px solid var(--photo-frame);
    background:
      radial-gradient(ellipse 55% 65% at 45% 45%, var(--photo-light) 0%, var(--photo-mid) 50%, transparent 85%),
      linear-gradient(135deg, var(--photo-dark) 0%, #7d8a5e 50%, #6a5444 100%);
  }
  .details {
    position: absolute;
    left: 62px;
    top: 264px;
  }
  .name {
    font-size: 29px;
    font-weight: 700;
    color: var(--pink-deep);
    letter-spacing: 0.5px;
    line-height: 1.1;
  }
  .role {
    font-size: 20px;
    font-weight: 700;
    color: var(--ink);
    letter-spacing: 0.8px;
    margin-bottom: 14px;
  }
  .contact-list { list-style: none; }
  .contact-item {
    display: flex;
    align-items: center;
    gap: 14px;
    font-size: 20px;
    color: var(--ink);
    line-height: 30px;
  }
  .contact-icon {
    width: 20px;
    height: 20px;
    flex: none;
  }
  .social-mark {
    width: 18px;
    height: 18px;
    margin: 0 1px;
    background: var(--pink);
    border-radius: 3px;
    flex: none;
  }
  .services {
    margin-top: 14px;
    font-size: 20px;
    color: var(--ink);
  }
</style>
</head>
<body>
<div class="canvas">
  <section class="business-card">
    <div class="portrait" role="img" aria-label="Portrait photo of the trainer, smiling outdoors"></div>
    <div class="details">
      <h1 class="name">TESSA BROGAN</h1>
      <p class="role">PERSONAL TRAINER</p>
      <ul class="contact-list">
        <li class="contact-item">
          <svg class="contact-icon" viewBox="0 0 24 24" aria-hidden="true">
            <path fill="#eea4c8" d="M6.6 10.8c1.4 2.8 3.8 5.1 6.6 6.6l2.2-2.2c.3-.3.7-.4 1-.2 1.1.4 2.3.6 3.6.6.6 0 1 .4 1 1V20c0 .6-.4 1-1 1C10.6 21 3 13.4 3 4c0-.6.4-1 1-1h3.5c.6 0 1 .4 1 1 0 1.3.2 2.5.6 3.6.1.3 0 .7-.2 1z"/>
          </svg>
          <span>07700218493</span>
        </li>
        <li class="contact-item">
          <svg class="contact-icon" viewBox="0 0 24 24" aria-hidden="true">
            <rect x="2" y="5" width="20" height="14" rx="2" fill="#eea4c8"/>
            <path d="M3 6.5l9 6.5 9-6.5" fill="none" stroke="#fff" stroke-width="1.8"/>
          </svg>
          <span>tessa.brogan@quellmail.com</span>
        </li>
        <li class="contact-item">
          <span class="social-mark" aria-hidden="true"></span>
          <span>Mira Bloom</span>
        </li>
      </ul>
      <p class="services">PT sessions, bootcamps.</p>
    </div>
  </section>
</div>
</body>
</html>
```